NEW Modern Sleek Business Card for VR Language Startup

Our startup is using VR to lead the next wave of world language education. We need a two-sided business card that introduces the larger organization (Brightloom Language Inc) and our contact info on one side and shows the product, Glimwoorld, on the other side.

Side 1 (contact info)= Brightloom Logo and Contact info (name, title, phone, email)

Side 2 (product)= Glimworld logo, text, and website
Text= Culturally Immersive Language Learning Games
Website= www.glimworld-play.com

Target Market(s)

Education, Technology

Contact Information for Business Card

Contact info will be updated upon approval of the design. For now, put this as a placeholder.

Perry Dunmore
Founder & CEO
pdunmore@quillpost-mail.net
(555)-014-2286

Font styles to use
Other font styles liked:
• Gibson and Century Gothic are the brand fonts

Requirements
Nice to have
• I would love to see cohesion between the design and colors of the two logos. I have attached a few business card designs that I like, so you can get a feel for my preferred style.

```html
<!DOCTYPE html>
<html lang="en">
<head>
<meta charset="UTF-8">
<title>Glimworld / Brightloom Language – Business Card</title>
<link rel="stylesheet" href="https://fonts.googleapis.com/css2?family=Poppins:wght@300;500;600;700&family=Questrial&display=swap">
<style>
  :root {
    --bg: #e8e8ee;
    --cyan: #4cc6e6;
    --violet: #6c5bb0;
    --magenta: #b04a9e;
    --pink: #e23e6a;
    --blue: #3aaee6;
    --ink: #111114;
    --paper: #ffffff;
    --shadow: 0 18px 40px rgba(30, 30, 60, 0.18);
  }
  * { box-sizing: border-box; margin: 0; padding: 0; }
  html, body { width: 1200px; height: 800px; overflow: hidden; }
  body {
    background: var(--bg);
    font-family: "Questrial", "Century Gothic", sans-serif;
    position: relative;
  }
  .card {
    position: absolute;
    width: 520px;
    height: 300px;
    border-radius: 18px;
    overflow: hidden;
    box-shadow: var(--shadow);
  }

  /* Product side */
  .card--product {
    left: 70px;
    top: 130px;
    background: linear-gradient(135deg, var(--cyan) 0%, #5fa6da 45%, var(--violet) 100%);
    color: var(--paper);
    display: flex;
    flex-direction: column;
    align-items: center;
    justify-content: center;
    text-align: center;
  }
  .product-mark {
    display: flex;
    align-items: center;
    gap: 14px;
    margin-bottom: 14px;
  }
  .product-mark__dot {
    width: 38px; height: 38px;
    border-radius: 50%;
    background: var(--paper);
  }
  .product-mark__name {
    font-family: "Questrial", "Century Gothic", sans-serif;
    font-size: 54px;
    line-height: 1;
    color: var(--paper);
  }
  .product-tagline {
    font-size: 19px;
    letter-spacing: 0.2px;
  }
  .product-url {
    font-size: 16px;
    margin-top: 4px;
  }

  /* Contact side */
  .card--contact {
    left: 610px;
    top: 370px;
    background: var(--paper);
  }
  .card__art { position: absolute; inset: 0; }
  .org-mark {
    position: absolute;
    left: 22px;
    top: 150px;
    display: flex;
    align-items: center;
    gap: 9px;
    color: var(--paper);
  }
  .org-mark__dot {
    width: 30px; height: 30px;
    border-radius: 50%;
    background: var(--paper);
    flex: none;
  }
  .org-mark__name {
    font-family: "Poppins", sans-serif;
    font-weight: 700;
    font-size: 23px;
    letter-spacing: 1.5px;
    line-height: 1;
  }
  .org-mark__sub {
    display: block;
    font-family: "Poppins", sans-serif;
    font-weight: 700;
    font-size: 10px;
    letter-spacing: 8px;
    margin-top: 6px;
  }
  .contact {
    position: absolute;
    left: 285px;
    top: 26px;
    width: 220px;
    text-align: center;
    color: var(--ink);
  }
  .contact__name {
    font-family: "Poppins", sans-serif;
    font-weight: 600;
    font-size: 20px;
    letter-spacing: 0.5px;
    line-height: 1.1;
  }
  .contact__title {
    font-family: "Poppins", sans-serif;
    font-weight: 500;
    font-size: 14px;
    background: linear-gradient(90deg, var(--pink), var(--violet), var(--blue));
    -webkit-background-clip: text;
    background-clip: text;
    color: transparent;
  }
  .contact__icon { display: block; margin: 12px auto 4px; }
  .contact__line {
    font-size: 14px;
    font-family: "Poppins", sans-serif;
    font-weight: 500;
  }
  .contact__line--small { font-size: 12.5px; }
  .contact__rule {
    height: 1.5px;
    margin: 10px 6px 0;
    background: linear-gradient(90deg, var(--pink), var(--violet), var(--blue));
  }
  .contact__web {
    margin-top: 14px;
    font-family: "Poppins", sans-serif;
    font-weight: 600;
    font-size: 14px;
    letter-spacing: 0.5px;
  }
  .contact__web-name { color: var(--violet); }
</style>
</head>
<body>

  <section class="card card--product" aria-label="Product side">
    <div class="product-mark">
      <span class="product-mark__dot"></span>
      <span class="product-mark__name">Glimworld</span>
    </div>
    <p class="product-tagline">Culturally Immersive Language Learning Games</p>
    <p class="product-url">www.glimworld-play.com</p>
  </section>

  <section class="card card--contact" aria-label="Contact side">
    <svg class="card__art" viewBox="0 0 520 300" width="520" height="300" aria-hidden="true">
      <defs>
        <linearGradient id="panelGrad" x1="0" y1="0" x2="1" y2="1">
          <stop offset="0" stop-color="#e23e6a"/>
          <stop offset="0.45" stop-color="#8e4fb0"/>
          <stop offset="0.75" stop-color="#6c6bc4"/>
          <stop offset="1" stop-color="#3ec0ea"/>
        </linearGradient>
      </defs>
      <path d="M0 40 H205 Q248 40 248 83 V300 H0 Z" fill="url(#panelGrad)"/>
      <path d="M0 30 H212 Q258 30 258 76 V300" fill="none" stroke="#111114" stroke-width="5"/>
    </svg>

    <div class="org-mark">
      <span class="org-mark__dot"></span>
      <div>
        <span class="org-mark__name">BRIGHTLOOM</span>
        <span class="org-mark__sub">LANGUAGE</span>
      </div>
    </div>

    <div class="contact">
      <p class="contact__name">PERRY DUNMORE</p>
      <p class="contact__title">Founder &amp; CEO</p>

      <svg class="contact__icon" width="24" height="24" viewBox="0 0 24 24" aria-hidden="true">
        <defs>
          <linearGradient id="iconGrad" x1="0" y1="0" x2="1" y2="1">
            <stop offset="0" stop-color="#e23e6a"/>
            <stop offset="1" stop-color="#3aaee6"/>
          </linearGradient>
        </defs>
        <circle cx="12" cy="12" r="10.5" fill="none" stroke="url(#iconGrad)" stroke-width="2"/>
        <path d="M8.2 7.5 L10 7.3 L11 9.6 L9.9 10.5 Q10.9 12.6 13.3 13.9 L14.3 12.9 L16.6 13.9 L16.4 15.7 Q11 16.5 8 10.2 Z" fill="#111114"/>
      </svg>
      <p class="contact__line">(555)-014-2286</p>
      <div class="contact__rule"></div>

      <svg class="contact__icon" width="24" height="24" viewBox="0 0 24 24" aria-hidden="true">
        <circle cx="12" cy="12" r="10.5" fill="none" stroke="url(#iconGrad)" stroke-width="2"/>
        <rect x="6.5" y="8.5" width="11" height="7.5" rx="1" fill="#111114"/>
        <polyline points="6.8,9 12,12.8 17.2,9" fill="none" stroke="#ffffff" stroke-width="1.2"/>
      </svg>
      <p class="contact__line contact__line--small">pdunmore@quillpost-mail.net</p>

      <p class="contact__web">www.<span class="contact__web-name">glimworld-play</span>.com</p>
    </div>
  </section>

</body>
</html>
```